Brindle Recycling needs a new web design

We need a new web design for our company based in Austin, TX. We resell and recycling electronics such as laptops, computer components, Zelvotabs, Quorns, etc. Since our inception over ten years ago, we’ve become one of the premier electronics recycling and remarketing companies in Austin, Texas.

```html
<!DOCTYPE html>
<html lang="en">
<head>
<meta charset="utf-8">
<title>Brindle Recycling</title>
<link href="https://fonts.googleapis.com/css2?family=Poppins:wght@400;500;600;700&display=swap" rel="stylesheet">
<style>
:root{
  --blue:#1c5aa8;
  --blue-dark:#154a8f;
  --orange:#f4623a;
  --navy:#2c3646;
  --ink:#333a44;
  --muted:#6b7380;
  --gray:#ececec;
  --line:#c9ced6;
  --white:#ffffff;
}
*{box-sizing:border-box;margin:0;padding:0}
html,body{width:1200px;height:3600px;overflow:hidden;background:var(--white)}
body{position:relative;font-family:'Poppins',sans-serif;color:var(--ink)}
.abs{position:absolute}
.btn{position:absolute;display:flex;align-items:center;justify-content:center;background:var(--blue);color:var(--white);font-weight:600;font-size:14px;letter-spacing:.5px;text-transform:uppercase}

/* top bar */
.topbar{left:0;top:0;width:1200px;height:43px;background:var(--navy)}
.social{top:12px;width:19px;height:19px;border-radius:50%;background:var(--white)}
.tollfree{left:650px;top:0;line-height:43px;color:var(--white);font-size:13px;font-weight:500}
.pickup-btn{left:907px;top:0;width:159px;height:43px;font-size:12px}

/* header */
.header{left:0;top:43px;width:1200px;height:101px;background:var(--white)}
.brand{display:flex;align-items:center;gap:12px}
.brand-mark{width:46px;height:46px;border-radius:50%;border:4px solid var(--blue)}
.brand-name{font-weight:700;color:var(--blue);font-size:24px;letter-spacing:.3px}
.nav{left:488px;top:43px;height:101px;display:flex;align-items:center;gap:34px;font-size:13px;font-weight:500;text-transform:uppercase;color:#222}
.nav .active{color:var(--blue)}

/* hero */
.hero{left:0;top:144px;width:1200px;height:480px;background:linear-gradient(110deg,#3a3f47 0%,#1e2329 45%,#101318 100%)}
.hero-title{right:134px;top:262px;text-align:right;color:var(--white);font-size:36px;font-weight:600;line-height:1.2;text-transform:uppercase}
.hero-text{right:134px;top:362px;width:400px;text-align:right;color:var(--white);font-size:13px;line-height:1.85}
.hero-btn{left:926px;top:470px;width:140px;height:43px;background:#e8e8e8;color:#333;font-size:13px}
.dot{left:1019px;width:10px;height:10px;border-radius:50%;background:var(--white)}

/* section headings */
.eyebrow{display:flex;align-items:center;gap:10px;font-size:17px;color:var(--ink);text-transform:uppercase}
.eyebrow::before{content:"";width:30px;height:2px;background:var(--ink)}
.heading{color:var(--blue);font-weight:600;font-size:28px;text-transform:uppercase}
.body-text{font-size:13.5px;line-height:2;color:var(--ink)}

/* about */
.bio-block{left:648px;top:876px;width:209px;height:247px;background:var(--blue)}
.bio-image{left:734px;top:682px;width:332px;height:386px;background:radial-gradient(circle at 50% 55%,#6f8a55 0%,#8fb8d8 40%,#bcdaf1 80%)}
.play{left:884px;top:1134px;width:44px;height:44px;border-radius:50%;background:var(--blue)}
.play-label{left:943px;top:1146px;font-size:12px;font-weight:600;color:var(--blue);text-transform:uppercase}

/* services */
.services{left:0;top:1260px;width:1200px;height:612px;background:var(--gray)}
.card{position:absolute;top:1471px;height:305px;text-align:center;color:var(--white);padding:0 20px}
.card-icon{width:76px;height:76px;border-radius:50%;background:var(--white);margin:20px auto 28px;display:flex;align-items:center;justify-content:center}
.card h3{font-size:15.5px;font-weight:700;text-transform:uppercase}
.card .tag{font-size:11px;font-style:italic;text-transform:uppercase;margin:4px 0 16px;font-weight:500}
.card p{font-size:12px;line-height:1.75}
.card .cta{display:block;margin-top:12px;font-weight:700;font-size:14px}

/* ceo */
.ceo-photo{left:192px;top:1951px;width:336px;height:461px;background:linear-gradient(180deg,#e9edf1 0%,#dfe5ec 55%,#9fb7d8 100%);box-shadow:0 6px 18px rgba(0,0,0,.25)}

/* overview */
.overview{left:0;top:2443px;width:1200px;height:427px;background:var(--gray)}
.feature h4{font-size:16.5px;font-weight:600;color:var(--blue);text-transform:uppercase;margin-bottom:12px}
.feature li{list-style:none;display:flex;align-items:flex-start;gap:10px;font-size:12.5px;line-height:1.55;margin-bottom:6px}
.feature li::before{content:"";flex:none;width:12px;height:12px;margin-top:3px;border-radius:50%;border:3px solid var(--blue)}

/* contact form */
.field{position:absolute;border:1px solid #b9bec6;background:var(--white);font-size:12.5px;color:#777;padding:14px 22px}

/* footer */
.footer{left:0;top:3252px;width:1200px;height:269px;background:var(--gray)}
.foot-h{font-size:16px;font-weight:600;color:var(--blue);text-transform:uppercase}
.foot-list{font-size:12.5px;line-height:1.75;color:var(--ink);list-style:none}
.contact-row{display:flex;align-items:flex-start;gap:14px;font-size:12.5px;line-height:1.6;margin-bottom:12px}
.contact-row svg{flex:none;margin-top:3px}
.news p{font-size:12.5px;line-height:1.55}
.news time{display:block;font-size:11px;font-style:italic;color:var(--muted);margin-bottom:10px}
.bottombar{left:0;top:3521px;width:1200px;height:79px;background:var(--blue);color:var(--white);font-size:12.5px;display:flex;align-items:center;justify-content:center}
</style>
</head>
<body>

<!-- top bar -->
<div class="abs topbar"></div>
<span class="abs social" style="left:132px"></span>
<span class="abs social" style="left:158px"></span>
<span class="abs social" style="left:184px"></span>
<div class="abs tollfree">TOLL FREE: (844)55-BRIND (27463)</div>
<div class="btn pickup-btn">Schedule a Pickup</div>

<!-- header -->
<div class="abs header"></div>
<div class="abs brand" style="left:132px;top:70px">
  <span class="brand-mark"></span>
  <span class="brand-name">Brindle Recycling</span>
</div>
<nav class="abs nav">
  <span class="active">Home</span><span>About Us</span><span>Page</span><span>Services</span><span>Certificate</span><span>Contact Us</span>
  <svg width="18" height="18" viewBox="0 0 18 18"><circle cx="7.5" cy="7.5" r="5.5" fill="none" stroke="#1c5aa8" stroke-width="2.4"/><line x1="11.5" y1="11.5" x2="16" y2="16" stroke="#1c5aa8" stroke-width="2.6" stroke-linecap="round"/></svg>
</nav>

<!-- hero -->
<div class="abs hero" role="img" aria-label="Close-up photo of a hand working on a computer circuit board"></div>
<svg class="abs" style="left:0;top:560px" width="1200" height="66" viewBox="0 0 1200 66" preserveAspectRatio="none"><path d="M0 40 C300 70 600 80 850 50 C1000 30 1100 10 1200 0 L1200 66 L0 66 Z" fill="#ffffff"/></svg>
<h1 class="abs hero-title">Computer Recycling<br>Made Easy</h1>
<p class="abs hero-text">Want to make a difference to our environment and planet? Brindle Recycling is here to help! Brindle Recycling has been helping keep the environment healthy since 2006</p>
<div class="btn hero-btn">Read More</div>
<span class="abs dot" style="top:532px;width:12px;height:12px;left:1018px;border:2px solid #fff;background:transparent"></span>
<span class="abs dot" style="top:552px;width:7px;height:7px;left:1021px"></span>
<span class="abs dot" style="top:566px;width:7px;height:7px;left:1021px"></span>

<!-- about bio -->
<div class="abs eyebrow" style="left:138px;top:773px">About</div>
<h2 class="abs heading" style="left:138px;top:800px">Company Bio</h2>
<p class="abs body-text" style="left:132px;top:858px;width:430px">What most people do not realize is electronic waste represents 2% of America's trash in landfills, but it equals 70% of overall toxic waste. Used computer equipment is a rapidly growing source of waste across the country. Only 12.5% of electronic waste is currently recycled in the US.</p>
<div class="btn" style="left:132px;top:1010px;width:137px;height:48px">Read More</div>
<div class="abs bio-block"></div>
<div class="abs bio-image" role="img" aria-label="Illustration of a small green planet with trees, buildings and clouds"></div>
<div class="abs play"><svg width="44" height="44" viewBox="0 0 44 44"><path d="M17 13 L31 22 L17 31 Z" fill="#fff"/></svg></div>
<div class="abs play-label">See How We Work</div>

<!-- services -->
<div class="abs services"></div>
<h2 class="abs heading" style="left:0;width:1200px;text-align:center;top:1312px">Our Services</h2>
<p class="abs body-text" style="left:260px;width:680px;text-align:center;top:1374px;font-size:14px">Sed ut perspiciatis unde omnis iste natus error sit voluptatem accusantium doloremque laudantium, totam rem aperiam, eaque ipsa quae ab</p>
<div class="abs" style="left:149px;top:1471px;width:391px;height:305px;background:linear-gradient(135deg,#0e2f6b 0%,#2f62b8 45%,#6a8fc9 70%,#17306a 100%)" role="img" aria-label="Photo of a blue computer circuit board"></div>
<div class="card" style="left:576px;width:230px;background:var(--orange)">
  <div class="card-icon"><svg width="40" height="36" viewBox="0 0 40 36"><rect x="4" y="3" width="32" height="22" rx="2" fill="#1c5aa8"/><rect x="8" y="7" width="24" height="14" fill="#fff"/><rect x="17" y="25" width="6" height="5" fill="#1c5aa8"/><rect x="11" y="30" width="18" height="3" fill="#1c5aa8"/></svg></div>
  <h3>Electronic Recycling</h3>
  <div class="tag">Environmentally Friendly</div>
  <p>At Brindle Recycling, we strive to keep the environment clean through our wide range of services.</p>
  <span class="cta">Schedule a Pickup</span>
</div>
<div class="card" style="left:821px;width:230px;background:var(--blue)">
  <div class="card-icon"><span style="width:46px;height:46px;border-radius:50%;border:4px solid var(--blue)"></span></div>
  <h3>Recycling Pickup</h3>
  <div class="tag">We Come To You</div>
  <p>At Brindle Recycling, we go out of our way to make sure your recycling process is made easy as possible.</p>
  <span class="cta">Schedule a Pickup</span>
</div>

<!-- ceo -->
<div class="abs ceo-photo" role="img" aria-label="Portrait photo of the company CEO in a shirt and tie"></div>
<div class="abs eyebrow" style="left:629px;top:2023px">About</div>
<h2 class="abs heading" style="left:629px;top:2050px">Company CEO</h2>
<p class="abs body-text" style="left:631px;top:2100px;width:410px">As the CEO of Brindle Recycling, Grant Hollis is responsible for running all facets of the business. Grant has a proven executive management track record and over 20 years of experience driving sales growth in the Recycling industry.</p>
<div class="abs" style="left:631px;top:2214px;font-size:18px;font-weight:600;color:var(--blue)">Grant Hollis</div>
<div class="abs" style="left:631px;top:2244px;font-size:13.5px">President</div>
<div class="btn" style="left:631px;top:2282px;width:137px;height:48px">Read More</div>

<!-- overview -->
<div class="abs overview"></div>
<h2 class="abs heading" style="left:134px;top:2535px;font-size:31px">Overview</h2>
<p class="abs body-text" style="left:134px;top:2593px;width:290px;font-size:13px;line-height:1.85">Sed ut perspiciatis unde omnis iste natus error sit voluptatem accusantium doloremque laudantium, totam rem aperiam, eaque ipsa</p>
<div class="btn" style="left:134px;top:2717px;width:159px;height:48px">Read More</div>

<svg class="abs" style="left:478px;top:2537px" width="48" height="48" viewBox="0 0 48 48"><path d="M24 6 A18 18 0 1 1 8 18" fill="none" stroke="#1c5aa8" stroke-width="6"/><path d="M2 14 L14 12 L10 24 Z" fill="#1c5aa8"/></svg>
<div class="abs feature" style="left:547px;top:2537px;width:220px"><h4>Recycling</h4><ul><li>Certified Global Recycling Capabilities</li><li>Sort by commodity</li></ul></div>

<svg class="abs" style="left:784px;top:2537px" width="52" height="40" viewBox="0 0 52 40"><rect x="2" y="8" width="30" height="20" fill="#1c5aa8"/><path d="M32 14 H42 L50 22 V28 H32 Z" fill="#1c5aa8"/><circle cx="12" cy="32" r="5" fill="#1c5aa8" stroke="#ececec" stroke-width="2"/><circle cx="40" cy="32" r="5" fill="#1c5aa8" stroke="#ececec" stroke-width="2"/></svg>
<div class="abs feature" style="left:854px;top:2537px;width:220px"><h4>Logistics</h4><ul><li>Global Warehouse Capabilities</li><li>Global Logistics Support</li></ul></div>

<svg class="abs" style="left:480px;top:2686px" width="44" height="52" viewBox="0 0 44 52"><circle cx="22" cy="20" r="17" fill="#1c5aa8"/><circle cx="22" cy="20" r="9" fill="none" stroke="#fff" stroke-width="2"/><path d="M12 34 L8 50 L16 46 L20 52 L22 38 Z M32 34 L36 50 L28 46 L24 52 L22 38 Z" fill="#1c5aa8"/></svg>
<div class="abs feature" style="left:547px;top:2688px;width:220px"><h4>Certificates</h4><ul><li>R2:2013 Responsible Recycling Certified</li><li>ISO 14001:2015</li></ul></div>

<svg class="abs" style="left:783px;top:2684px" width="50" height="50" viewBox="0 0 50 50"><circle cx="25" cy="25" r="21" fill="none" stroke="#1c5aa8" stroke-width="4"/><text x="25" y="34" text-anchor="middle" font-family="Poppins,sans-serif" font-size="26" font-weight="700" fill="#1c5aa8">$</text></svg>
<div class="abs feature" style="left:854px;top:2688px;width:220px"><h4>Return</h4><ul><li>Market Value Pricing</li><li>Profit Sharing</li></ul></div>

<!-- get in touch -->
<h2 class="abs heading" style="left:0;width:1200px;text-align:center;top:2912px">Get In Touch</h2>
<div class="field" style="left:216px;top:3010px;width:377px;height:55px">First Name</div>
<div class="field" style="left:216px;top:3079px;width:377px;height:53px">Email</div>
<div class="field" style="left:216px;top:3146px;width:377px;height:56px">Password</div>
<div class="field" style="left:610px;top:3010px;width:376px;height:122px">Message</div>
<div class="btn" style="left:612px;top:3151px;width:118px;height:43px;font-size:13px">Submit</div>

<!-- footer -->
<div class="abs footer"></div>
<div class="abs brand" style="left:132px;top:3358px">
  <span class="brand-mark"></span>
  <span class="brand-name" style="font-size:21px">Brindle Recycling</span>
</div>
<div class="abs foot-h" style="left:413px;top:3284px">Contact Us</div>
<div class="abs" style="left:413px;top:3330px;width:230px">
  <div class="contact-row"><svg width="12" height="16" viewBox="0 0 12 16"><path d="M6 0 A6 6 0 0 1 12 6 C12 10 6 16 6 16 C6 16 0 10 0 6 A6 6 0 0 1 6 0 Z" fill="#333a44"/><circle cx="6" cy="6" r="2.2" fill="#ececec"/></svg><span>4120 Larkspur Mill Rd.<br>Austin, Texas 78731</span></div>
  <div class="contact-row"><svg width="14" height="14" viewBox="0 0 14 14"><path d="M3 0 L6 3 L4 5 C5 7 7 9 9 10 L11 8 L14 11 L11 14 C5 13 1 9 0 3 Z" fill="#333a44"/></svg><span>(512)555-0147</span></div>
  <div class="contact-row"><svg width="14" height="14" viewBox="0 0 14 14"><rect x="1" y="5" width="12" height="8" fill="#333a44"/><rect x="3" y="1" width="8" height="4" fill="none" stroke="#333a44" stroke-width="1.5"/></svg><span>(512)555-0192</span></div>
  <div class="contact-row"><svg width="14" height="12" viewBox="0 0 14 12"><rect x="0" y="1" width="14" height="10" fill="#333a44"/><path d="M0 1 L7 7 L14 1" fill="none" stroke="#ececec" stroke-width="1.3"/></svg><span>Grant@BrindleRecycling.com</span></div>
</div>
<div class="abs foot-h" style="left:679px;top:3284px">Links</div>
<ul class="abs foot-list" style="left:681px;top:3330px"><li>Home</li><li>About us</li><li>Page</li><li>Services</li><li>Certificate</li><li>Contact us</li></ul>
<div class="abs foot-h" style="left:840px;top:3284px">Recent News</div>
<div class="abs news" style="left:842px;top:3330px;width:240px">
  <p>Sed ut perspiciatis unde omnis iste natus error sit vo</p><time>May 25, 2018</time>
  <p>Sed ut perspiciatis unde omnis iste natus error sit vo</p><time>May 25, 2018</time>
</div>

<div class="abs bottombar">© 2018 Brindle Recycling | All Rights Reserved</div>

</body>
</html>
```